AMBER AND SLATE WEB

We need a home design in wordpress, we have now a web but we would like to improve it. Our current web is www.amberandslatevillas.example Our business is holliday rental of villas in Ibiza. Our guest must know that we are a reliable company, professional and with experience and good reviews. We want them to click in our reservation engine: https://bookings.amberandslatevillas.example/en/ and make reservation in our website. We would also like to say that all the properties that we have are just us who commercialize so we have best price available. Many people are going to see our villas in staylist.example and look to our website to make a reservation with us so we need to show them that they are at the right place and click at our link to our reservation engine. What make us special is that we are a local company, we are from Ibiza, Our guests are always received in person by the Amber and Slate Ibiza team. You will enjoy extensive tourist information when you check in and during the entire stay. You will be attended by ChatterLine and calls, always happy to help so that you have a happy and fun stay! Our guest stay is better than in hotel as they have more spece, private swiming pool, private garden, barbeque ... To rent a villa is the best way to stay in Ibiza. We also have a promotional video: https://vidshare.example/Qm7TzR2pLxA Let our philosophy be shown, we think that coming on holiday to Ibiza implies seeing the nature that we have in Ibiza, hence our name AMBER AND SLATE, like the pins that almost touch the sea in Ibiza, or the posidonea meadows where the intense green of the seaweed and the blue of the sea. We are aware of the environment, and we love Ibiza. For us, the client who visits Ibiza, should rent a car, go around the island, eat in a restaurant one day in front of the sea, is a night of partying to the discs, go shopping, visit the ancient heritage of Umanity, make some aquatic sport, enjoy the pool, those are for us Ibiza.

Target Market(s)

Europe, people from Holand, UK, Germany, France, Spain ...

Industry/Entity Type

Tourism

Colors

Designer to choose colors to be used in the design.

Requirements
Must have
• Pictures of Ibiza.
Nice to have
• Our name Amber and Slate Ibiza is beacuse in Ibiza there is forest that almost touch the watter of the Mediterranean sea, so you can see green of the forest and blue of the sea and the sky. And also beacause under the watter of the sea there is a plant called Posidonia that is also green please see the picture of posidonia.

```html
<!DOCTYPE html>
<html lang="en">
<head>
<meta charset="utf-8">
<title>Amber and Slate Ibiza — Villas</title>
<link href="https://fonts.googleapis.com/css2?family=Montserrat:wght@400;600;700&family=Oswald:wght@500&family=Roboto:wght@400;500;700&display=swap" rel="stylesheet">
<style>
:root{
  --accent:#2fd39c;
  --link:#1fd6c8;
  --ink:#3a3a3a;
  --muted:#555;
  --white:#fff;
  --dark-btn:rgba(20,28,30,.82);
  --sea-deep:#0a63b8;
  --sea-light:#3fc6d8;
  --pine:#3f7a34;
}
*{box-sizing:border-box;margin:0;padding:0}
html,body{width:1200px;height:2415px;overflow:hidden;background:var(--white)}
body{position:relative;font-family:'Montserrat',sans-serif;color:var(--ink)}
.abs{position:absolute}

/* hero */
.hero{left:0;top:0;width:1200px;height:675px;
  background:
   radial-gradient(ellipse 380px 260px at 130px 520px,#3d7e2f 0%,rgba(61,126,47,0) 100%),
   radial-gradient(ellipse 360px 300px at 1100px 260px,#5b8a3a 0%,rgba(91,138,58,0) 100%),
   radial-gradient(ellipse 420px 200px at 860px 520px,#d9c9a2 0%,rgba(217,201,162,0) 100%),
   radial-gradient(ellipse 520px 260px at 560px 470px,#46d4df 0%,rgba(70,212,223,0) 100%),
   linear-gradient(180deg,#1c6fd6 0%,#2a8ee0 22%,#1a5fb0 34%,#1b79c2 55%,#3cc3d4 100%)}
.brand{left:89px;top:28px;display:flex;align-items:center;gap:8px;color:var(--white)}
.brand-dot{width:12px;height:12px;border-radius:50%;background:var(--white)}
.brand-name{font-family:'Montserrat',sans-serif;font-size:16px;font-weight:400;letter-spacing:.5px}
.nav{left:485px;top:58px;display:flex;align-items:center;gap:23px;font-size:10.5px;font-weight:700;color:var(--white)}
.nav .boxed{border:2px solid var(--white);padding:2px 5px}
.nav .solid{background:var(--white);color:#1c74d4;padding:4px 7px}
.hero-title{left:0;width:1200px;top:412px;text-align:center;font-family:'Oswald',sans-serif;font-weight:500;font-size:47px;color:var(--white);letter-spacing:1px}
.hero-btn{left:506px;top:528px;width:188px;height:63px;border:5px solid var(--white);color:var(--white);font-family:'Roboto',sans-serif;font-size:22px;font-weight:500;letter-spacing:1px;display:flex;align-items:center;justify-content:center}

/* section headings */
.sec-title{left:0;width:1200px;text-align:center;font-family:'Roboto',sans-serif;font-weight:500;font-size:18px;color:#333;letter-spacing:.5px;display:flex;align-items:center;justify-content:center;gap:42px}
.sec-title::before,.sec-title::after{content:"";width:48px;height:2px;background:var(--accent)}

.about-lead{left:230px;top:796px;width:740px;text-align:center;font-size:11.6px;line-height:15px;color:var(--muted)}
.about-lead b{color:var(--accent);font-weight:600}
.about-body{left:92px;top:889px;width:500px;font-size:11.6px;line-height:15px;color:var(--muted)}
.about-body p{margin-bottom:15px}
.about-body a{color:var(--link);text-decoration:none}
.card-back{background:var(--white);box-shadow:0 2px 10px rgba(0,0,0,.12)}
.about-photo{left:712px;top:876px;width:349px;height:232px;
  background:linear-gradient(180deg,#d8dfe6 0%,#f2e8d4 30%,#6b8fa8 48%,#a9865c 70%,#5e4a33 100%)}

/* deals */
.deal{overflow:hidden;border-radius:6px}
.deal-name{left:0;right:0;top:20px;text-align:center;font-family:'Roboto',sans-serif;font-weight:500;font-size:16px;line-height:19px;color:var(--white);position:absolute}
.deal-btn{position:absolute;left:50%;transform:translateX(-50%);bottom:16px;width:134px;height:37px;border-radius:5px;background:var(--dark-btn);color:var(--link);font-family:'Roboto',sans-serif;font-weight:700;font-size:17px;display:flex;align-items:center;justify-content:center}
.d1{left:87px;top:1268px;width:252px;height:407px;background:linear-gradient(180deg,#2f7fd9 0%,#3a8fd8 30%,#e2a43a 48%,#c88a2e 65%,#1d7fc8 85%,#1a6fb5 100%);border-radius:8px}
.d2{left:346px;top:1268px;width:446px;height:185px;background:linear-gradient(180deg,#6f9a5a 0%,#d9cbb4 35%,#2ab8e4 60%,#c9593a 100%)}
.d3{left:799px;top:1268px;width:312px;height:185px;background:linear-gradient(180deg,#3f8fe0 0%,#7db0d8 40%,#4d6a3e 60%,#d2d6d8 100%)}
.d4{left:346px;top:1460px;width:338px;height:215px;background:linear-gradient(180deg,#9a6a44 0%,#e9e2d6 40%,#d8cdb9 75%,#6b4a34 100%)}
.d5{left:691px;top:1460px;width:420px;height:215px;background:linear-gradient(180deg,#2d7fd8 0%,#6aa6df 40%,#e9eef0 60%,#3d6a2e 100%)}

/* testimonials */
.band{left:0;top:1784px;width:1200px;height:377px;
  background:linear-gradient(180deg,#0d3f6a 0%,#1a5a7c 35%,#2f6b4a 70%,#4f7a35 100%)}
.t-card{left:334px;top:1848px;width:533px;height:247px;background:var(--white);border-radius:14px}
.avatar{left:562px;top:1875px;width:76px;height:76px;border-radius:50%;background:linear-gradient(180deg,#cfd7df,#9fb2c2)}
.quote{font-family:Georgia,serif;font-size:110px;line-height:1;color:#d9d9d9;font-weight:700}
.t-text{left:425px;top:1978px;width:350px;text-align:center;font-size:13.4px;line-height:17px;color:#444;font-family:'Roboto',sans-serif}
.t-author{left:455px;top:2046px;font-family:'Roboto',sans-serif;font-size:13.4px;color:#222}

/* footer */
.f-head{font-family:'Roboto',sans-serif;font-size:8.5px;font-weight:500;color:#444;text-align:center;padding-bottom:4px;border-bottom:2px solid var(--accent)}
.f-text{font-size:8.5px;line-height:15px;color:#666}
.f-text b{color:#444}
.f-center{text-align:center;font-weight:600;color:#555}
.f-menu{font-size:9px;font-weight:600;color:#555;text-align:center;line-height:30px}
</style>
</head>
<body>

<header>
  <div class="abs hero" role="img" aria-label="Photo of a turquoise Ibiza cove with pine-covered cliffs, sailboats and a sandy beach"></div>
  <div class="abs brand"><span class="brand-dot"></span><span class="brand-name">AMBER AND SLATE</span></div>
  <nav class="abs nav">
    <span>HOME</span><span>EXPERIENCE</span><span>ABOUT US</span><span>CONTACT US</span>
    <span class="boxed">ALL PROPERTIES</span><span class="solid">BOOK NOW</span>
  </nav>
  <h1 class="abs hero-title">THE BEST WAY TO STAY IN IBIZA!</h1>
  <div class="abs hero-btn">BOOK NOW</div>
</header>

<section>
  <h2 class="abs sec-title" style="top:732px">ABOUT US</h2>
  <p class="abs about-lead"><b>Amber and Slate Villas Ibiza</b> is a company specialized in offering its clients accommodation in Villas on the countryside of Ibiza. Our guests enjoy the rural Ibiza, tranquility, relax, private pool, close to dream beaches and coves, the best restaurants, an unforgettable holiday for family or friends.</p>
  <div class="abs about-body">
    <p>Every day can be a <a>different experience</a>, <a>beach</a>, <a>restaurant</a>, <a>flea market</a>, <a>disco</a>, <a>hiking</a>, <a>kayaking</a>, <a>horseback riding</a>, <a>shopping</a>, <a>history</a>, <a>boat ride</a>! There is a lot of variety for all budgets!</p>
    <p>The maximum distances of the island are 41 kilometers from north to south and 15 kilometers from east to west, we always recommend renting a car. <a>Enjoy the freedom</a> to go where you prefer, without depending on schedules or public transportation.</p>
    <p>Each client is different, both for those who discover Ibiza for the first time and for those who have already been many times, it is a pleasure for us to share our favorite places with our guests and help them to make their experience very special.</p>
  </div>
  <div class="abs card-back" style="left:739px;top:909px;width:353px;height:228px"></div>
  <div class="abs card-back" style="left:721px;top:890px;width:353px;height:230px"></div>
  <div class="abs about-photo" role="img" aria-label="Photo of a sunset beach in Ibiza with an island on the horizon and agave plants"></div>
</section>

<section>
  <h2 class="abs sec-title" style="top:1191px">BEST DEALS</h2>
  <div class="abs deal d1" role="img" aria-label="Photo of a yellow villa with blue shutters and a pool"><div class="deal-name">Villa Can Pinar<br>Montblanc</div><div class="deal-btn">Book now</div></div>
  <div class="abs deal d2" role="img" aria-label="Photo of a villa pool with sun loungers and red flowers"><div class="deal-name">Villa Les Tres Palmes</div><div class="deal-btn">Book now</div></div>
  <div class="abs deal d3" role="img" aria-label="Photo of a villa terrace with a pool and garden"><div class="deal-name">Villa Can Serra</div><div class="deal-btn">Book now</div></div>
  <div class="abs deal d4" role="img" aria-label="Photo of a rustic living room with wooden beams"><div class="deal-name">Agroturismo Can Roig</div><div class="deal-btn">Book now</div></div>
  <div class="abs deal d5" role="img" aria-label="Photo of a white villa with a tower and palm garden"><div class="deal-name">Villa Can Serra</div><div class="deal-btn">Book now</div></div>
</section>

<section>
  <h2 class="abs sec-title" style="top:1731px">TESTIMONIALS</h2>
  <div class="abs band" role="img" aria-label="Underwater photo of green posidonia seagrass meadows in blue sea"></div>
  <svg class="abs" style="left:254px;top:1952px" width="26" height="42" viewBox="0 0 26 42"><path d="M22 2 3 21l19 19" fill="none" stroke="#fff" stroke-width="2.5"/></svg>
  <svg class="abs" style="left:920px;top:1952px" width="26" height="42" viewBox="0 0 26 42"><path d="M4 2l19 19L4 40" fill="none" stroke="#fff" stroke-width="2.5"/></svg>
  <div class="abs t-card"></div>
  <div class="abs avatar" role="img" aria-label="Portrait photo of the reviewer"></div>
  <div class="abs quote" style="left:356px;top:1935px">&ldquo;</div>
  <div class="abs quote" style="left:784px;top:2008px">&rdquo;</div>
  <p class="abs t-text">Lorem ipsum dolor sit amet, consectetur adipiscing elit, sed do eiusmod tempor incididunt ut labore et dolore magna aliqua.</p>
  <p class="abs t-author">— Jane Doe</p>
</section>

<footer>
  <div class="abs f-head" style="left:162px;top:2209px;width:48px">ABOUT US</div>
  <p class="abs f-text" style="left:90px;top:2254px;width:320px"><b>Amber and Slate Villas Ibiza</b> is a company specialized in offering its clients accommodation in Villas on the countryside of Ibiza. Our guests enjoy the rural Ibiza, tranquility, relax, private pool, close to dream beaches and coves, the best restaurants, an unforgettable holiday for family or friends.</p>
  <div class="abs f-head" style="left:601px;top:2209px;width:52px">CONTACT US</div>
  <p class="abs f-text f-center" style="left:500px;top:2247px;width:264px">Amber &amp; Slate Ibiza<br>CALLE DE LES PINEDES, 8,<br>SANTA EULARIA DES RIU, 07840,<br>IBIZA, Spain</p>
  <p class="abs f-text f-center" style="left:480px;top:2337px;width:304px">Email: reservas@amberandslatevillas.example</p>
  <div class="abs f-head" style="left:1037px;top:2209px;width:26px">MENU</div>
  <div class="abs f-menu" style="left:990px;top:2240px;width:122px">HOME<br>EXPERIENCE<br>ABOUT US<br>CONTACT US<br>ALL PROPERTIES</div>
</footer>

</body>
</html>
```